Lunelle Rosa Hair Fancy Business Card’s

I want my business cards to be elite, original and very classy. I want the business cards to match the colors of my logo and to match the design posted. I would love the design of the picture I posted

I want the card all white .
The dripping on the top of the card I want it to match the pink color in my logo that’s also posted .
I need my logo on the business card !
I need my Instagram- @lunelle.rosa.hair__
And my phone number - 555 207 3962

Target Market(s)

My target market is young woman age 23 to older woman to the age of 65
I want both older and younger women to love my design . I don’t want any cheap looking business cards

Industry/Entity Type

Hair And Beauty

Contact Information for Business Card

Add my logo
Add my Instagram- @lunelle.rosa.hair__
My number - 555 207 3962
My website- www.lunellerosahair.example

Font styles to use
Serif
Script

Colors
ffffff
e667a6
e34298

Requirements
Must have
• The business cards must have my logo, my number , my website, and my Instagram!
Nice to have
• Nice to have glitter words that match my logo
• The business cards must look classy and mature
• I want them to be very unique!!
Should not have
• Should not have any colors that doesn’t match my logo ! This is very important! Please

```html
<!DOCTYPE html>
<html lang="en">
<head>
<meta charset="utf-8">
<title>Lunelle Rosa Hair — Business Card</title>
<link rel="stylesheet" href="https://fonts.googleapis.com/css2?family=Playfair+Display:wght@400&family=Roboto:wght@300&display=swap">
<style>
  :root {
    --white: #ffffff;
    --pink: #e667a6;
    --pink-deep: #e34298;
    --pink-hot: #f35ba6;
    --pink-soft: #f487b6;
    --blush: #fdf3f8;
    --ink-grey: #8c8c8c;
    --stage: #ececec;
  }
  * { box-sizing: border-box; margin: 0; padding: 0; }
  html, body { width: 1200px; height: 1200px; overflow: hidden; }
  body { background: var(--stage); position: relative; font-family: "Roboto", sans-serif; }

  .card {
    position: absolute;
    left: 223px;
    width: 753px;
    height: 451px;
    background: var(--white);
    overflow: hidden;
    box-shadow: 0 6px 16px rgba(0,0,0,0.12);
  }
  .card--front { top: 112px; }
  .card--back { top: 637px; }
  .card__art { position: absolute; inset: 0; width: 100%; height: 100%; }

  .brand {
    position: absolute;
    font-family: "Playfair Display", serif;
    font-weight: 400;
    color: var(--pink-deep);
    white-space: nowrap;
    transform: translate(-50%, -50%);
  }
  .card--front .brand { left: 376px; top: 205px; font-size: 34px; }
  .card--back .brand { left: 187px; top: 227px; font-size: 28px; }

  .contact-list { position: absolute; left: 385px; top: 172px; list-style: none; }
  .contact-list__item {
    display: flex; align-items: center;
    height: 38px;
    font-weight: 300; font-size: 21px; color: var(--ink-grey);
    white-space: nowrap;
  }
  .contact-list__icon { width: 28px; height: 28px; margin-right: 20px; flex: none; }
</style>
</head>
<body>

<section class="card card--front">
  <svg class="card__art" viewBox="0 0 1213 726" preserveAspectRatio="none" aria-hidden="true">
    <defs>
      <linearGradient id="front-blob" x1="0" y1="1" x2="1" y2="0">
        <stop offset="0" stop-color="var(--pink-hot)"/>
        <stop offset="1" stop-color="var(--pink-soft)"/>
      </linearGradient>
    </defs>
    <circle cx="320" cy="380" r="330" fill="var(--blush)" opacity="0.7"/>
    <circle cx="1030" cy="560" r="340" fill="var(--blush)" opacity="0.7"/>
    <path d="M0 0 H293 C300 40 260 90 200 105 C150 120 110 118 60 112 C30 110 10 115 0 118 Z" fill="var(--pink-soft)"/>
    <path d="M787 0 H1213 V246 C1170 240 1120 210 1090 190 C1050 170 980 175 900 190 C830 200 775 170 770 100 C768 50 780 20 787 0 Z" fill="url(#front-blob)"/>
    <path d="M0 578 C80 535 180 515 240 523 C320 530 370 560 405 595 C470 660 560 710 630 726 H0 Z" fill="url(#front-blob)"/>
    <path d="M800 726 C850 690 920 670 1000 676 C1070 682 1130 700 1175 726 Z" fill="var(--pink-soft)"/>
  </svg>
  <h1 class="brand">Lunelle Rosa Hair</h1>
</section>

<section class="card card--back">
  <svg class="card__art" viewBox="0 0 1213 726" preserveAspectRatio="none" aria-hidden="true">
    <defs>
      <linearGradient id="back-blob" x1="0" y1="0" x2="1" y2="0">
        <stop offset="0" stop-color="var(--pink-soft)"/>
        <stop offset="1" stop-color="var(--pink-hot)"/>
      </linearGradient>
      <linearGradient id="fold-shade" x1="0" y1="0" x2="1" y2="0">
        <stop offset="0" stop-color="#000" stop-opacity="0"/>
        <stop offset="0.5" stop-color="#000" stop-opacity="0.04"/>
        <stop offset="1" stop-color="#000" stop-opacity="0"/>
      </linearGradient>
    </defs>
    <circle cx="890" cy="330" r="280" fill="var(--blush)" opacity="0.7"/>
    <circle cx="260" cy="440" r="250" fill="var(--blush)" opacity="0.6"/>
    <rect x="580" y="60" width="60" height="620" fill="url(#fold-shade)"/>
    <path d="M0 0 H425 C440 40 450 100 430 140 C405 190 350 200 290 193 C220 186 150 170 100 200 C70 225 40 240 0 247 Z" fill="url(#back-blob)"/>
    <path d="M918 0 H1213 V117 C1170 125 1120 122 1080 110 C1000 90 950 80 925 50 C912 30 914 10 918 0 Z" fill="var(--pink-soft)"/>
    <path d="M578 726 C670 700 750 650 810 590 C860 540 960 515 1030 523 C1100 530 1160 555 1213 578 V726 Z" fill="url(#back-blob)"/>
    <path d="M38 726 C100 695 180 675 260 677 C320 680 370 700 415 726 Z" fill="var(--pink-soft)"/>
  </svg>
  <h2 class="brand">Lunelle Rosa Hair</h2>
  <ul class="contact-list">
    <li class="contact-list__item">
      <svg class="contact-list__icon" viewBox="0 0 24 24" aria-hidden="true">
        <path d="M6.5 3 L9.5 3 L11 7.5 L8.8 9.2 C9.8 11.6 12.4 14.2 14.8 15.2 L16.5 13 L21 14.5 L21 17.5 C21 19.4 19.4 21 17.5 21 C9.5 20.5 3.5 14.5 3 6.5 C3 4.6 4.6 3 6.5 3 Z" fill="none" stroke="var(--pink-hot)" stroke-width="1.8" stroke-linejoin="round"/>
      </svg>
      555 207 3962
    </li>
    <li class="contact-list__item">
      <svg class="contact-list__icon" viewBox="0 0 24 24" aria-hidden="true">
        <circle cx="12" cy="12" r="10" fill="var(--pink-hot)"/>
      </svg>
      @lunelle.rosa.hair__
    </li>
    <li class="contact-list__item">
      <svg class="contact-list__icon" viewBox="0 0 24 24" aria-hidden="true">
        <circle cx="12" cy="12" r="10" fill="none" stroke="var(--pink-hot)" stroke-width="1.8"/>
        <ellipse cx="12" cy="12" rx="4.5" ry="10" fill="none" stroke="var(--pink-hot)" stroke-width="1.4"/>
        <path d="M2 12 H22 M4 7 H20 M4 17 H20" stroke="var(--pink-hot)" stroke-width="1.4"/>
      </svg>
      www.lunellerosahair.example
    </li>
  </ul>
</section>

</body>
</html>
```